Business card design Needed for new logo / Construction business, home extensions and new builds

We need a business card design using our new logo files which i will attach to this project :)

We are a small construction business specialising in home extensions, new builds and property development. We are very ambitious and would appreciate professional and elegant designs for our new business card.

Very serious about using the services on MakerQuarry and recently acquired our new logo from here :)

Please get involved, i will feedback when i can as i am very busy but can respond daily, thanks

Target Market(s)

People that want to build onto their houses, new building developments or adding too their existing property

Industry/Entity Type

Construction

Contact Information for Business Card

Renwick Tolliver Construction, Lionel Ashby (Managing Director), Tel 07822254961, email - info@renwick-tolliver, www.renwick-tolliver.co.uk

Colors

Designer to choose colors to be used in the design.

Requirements
Must have
• I like a deep grey on the back please. A lot of you have provided black from and back, try mixing things up a little. The black looks cool 😎 Thanks

```html
<!DOCTYPE html>
<html lang="en">
<head>
<meta charset="utf-8">
<title>Renwick Tolliver Construction – Business Card</title>
<link rel="stylesheet" href="https://fonts.googleapis.com/css2?family=Cinzel:wght@400;600&family=Tinos&display=swap">
<style>
  :root {
    --backdrop: #262626;
    --card-front: #ffffff;
    --card-back: #6b6b6b;
    --gold: #c9963a;
    --gold-light: #f3cf86;
    --gold-deep: #b9822e;
    --silver: #c4c7ca;
    --ink: #2b2b2b;
  }
  * { margin: 0; padding: 0; box-sizing: border-box; }
  html, body { width: 1200px; height: 770px; overflow: hidden; }
  body { background: var(--backdrop); position: relative; }

  .card {
    position: absolute;
    top: 228px;
    overflow: hidden;
    box-shadow: 0 14px 22px rgba(0, 0, 0, 0.55);
  }
  .card--front { left: 35px; width: 549px; height: 311px; background: var(--card-front); }
  .card--back { left: 611px; width: 554px; height: 314px; background: var(--card-back); }

  .brand-art {
    position: absolute;
    top: 0;
    bottom: 0;
    width: 168px;
    background: linear-gradient(160deg, var(--silver) 0%, var(--gold-light) 38%, var(--gold) 70%, var(--gold-deep) 100%);
  }
  .card--front .brand-art { right: 0; }
  .card--back .brand-art { left: 0; }

  .wordmark {
    position: absolute;
    font-family: "Cinzel", serif;
    font-weight: 600;
    color: var(--gold);
    text-align: center;
    line-height: 1;
    white-space: nowrap;
  }
  .wordmark__name { display: block; font-size: 22px; letter-spacing: 0.6px; }
  .wordmark__sub {
    display: flex;
    align-items: center;
    justify-content: center;
    gap: 9px;
    font-size: 16px;
    letter-spacing: 1px;
    margin-top: 6px;
  }
  .wordmark__sub::before,
  .wordmark__sub::after {
    content: "";
    width: 22px;
    height: 1.5px;
    background: var(--gold);
  }
  .card--front .wordmark { left: 27px; top: 50px; }
  .card--back .wordmark { left: 381px; top: 192px; transform: translateX(-50%); }

  .brand-square {
    position: absolute;
    left: 375px;
    top: 160px;
    width: 12px;
    height: 12px;
    background: var(--gold);
  }

  .holder { position: absolute; left: 27px; top: 148px; }
  .holder__tab {
    position: absolute;
    left: -27px;
    top: 2px;
    width: 13px;
    height: 31px;
    background: linear-gradient(180deg, var(--gold-light), var(--gold));
    border-radius: 0 2px 2px 0;
  }
  .holder__name {
    font-family: "Cinzel", serif;
    font-weight: 600;
    font-size: 19px;
    color: var(--gold);
    letter-spacing: 0.4px;
  }
  .holder__role {
    font-family: "Tinos", serif;
    font-size: 14px;
    color: var(--ink);
    margin-top: 1px;
  }

  .contacts {
    position: absolute;
    left: 27px;
    top: 218px;
    list-style: none;
    font-family: "Tinos", serif;
    font-size: 14px;
    color: var(--ink);
  }
  .contacts li { display: flex; align-items: center; height: 24px; }
  .contacts svg { width: 10px; height: 10px; margin-right: 6px; fill: var(--gold); }
</style>
</head>
<body>

<section class="card card--front" aria-label="Business card front">
  <div class="brand-art" role="img" aria-label="Large gold and silver brand emblem decoration"></div>

  <div class="wordmark">
    <span class="wordmark__name">Renwick Tolliver</span>
    <span class="wordmark__sub">Construction</span>
  </div>

  <div class="holder">
    <span class="holder__tab"></span>
    <div class="holder__name">Lionel Ashby</div>
    <div class="holder__role">Managing Director</div>
  </div>

  <ul class="contacts">
    <li>
      <svg viewBox="0 0 10 10" aria-hidden="true"><path d="M2 0.5 3.6 2.6 2.7 3.6c.6 1.5 1.8 2.7 3.3 3.3l1-.9L9.5 7.6 8.4 9.5C4.3 9.2.8 5.7.5 1.6Z"/></svg>
      07822254961
    </li>
    <li>
      <svg viewBox="0 0 10 10" aria-hidden="true"><path d="M0 2.5h10v6H0Zm1 .6 4 3 4-3v-.1H1Z"/></svg>
      info@renwick-tolliver
    </li>
    <li>
      <svg viewBox="0 0 10 10" aria-hidden="true"><circle cx="5" cy="5" r="4.6" fill="none" stroke="#c9963a" stroke-width="1.2"/><path d="M0.6 5h8.8M5 .5c-2 2.7-2 6.3 0 9M5 .5c2 2.7 2 6.3 0 9" fill="none" stroke="#c9963a" stroke-width="0.8"/></svg>
      www.renwick-tolliver.co.uk
    </li>
  </ul>
</section>

<section class="card card--back" aria-label="Business card back">
  <div class="brand-art" role="img" aria-label="Large gold and silver brand emblem decoration"></div>

  <span class="brand-square"></span>
  <div class="wordmark">
    <span class="wordmark__name">Renwick Tolliver</span>
    <span class="wordmark__sub">Construction</span>
  </div>
</section>

</body>
</html>
```